Verlindo Magician

I want the business card for my business to give to people who watch that later I will be employed to show magic here is my website http://www.balsamomagicien.com/I want the interesting design , i am very opened for formal and informal, I watch a lot of design so don't stick to the common shape and form but i hope it can also be produced the thing to write on will be the same as in picture that i will upload , i also will upload the logo for you that so can be easy to useDenis CostilleMagicianMAGICIAN BALSAMO 17 rue des Tilleuls - 25000 BESANÇON contact@verlindoillusions.example tel. 0381 946 157 tel. 0674 219 503

```html
<!DOCTYPE html>
<html lang="en">
<head>
<meta charset="utf-8">
<title>Verlindo Magician – Business Card</title>
<link href="https://fonts.googleapis.com/css2?family=Jost:wght@300;400&display=swap" rel="stylesheet">
<style>
  :root {
    --backdrop: #e2e1df;
    --card-black: #000000;
    --card-white: #ffffff;
    --accent-red: #e0262b;
    --text-white: #ffffff;
    --text-black: #111111;
    --rule: #d8d8d8;
  }
  * { margin: 0; padding: 0; box-sizing: border-box; }
  html, body {
    width: 1125px; height: 1200px; overflow: hidden;
    background: var(--backdrop);
    font-family: "Jost", "Futura", sans-serif;
  }
  .canvas { position: relative; width: 1125px; height: 1200px; }
  .card {
    position: absolute; left: 166px; width: 800px; height: 456px;
  }
  .card--front { top: 103px; background: var(--card-black); color: var(--text-white); }
  .card--back { top: 619px; background: var(--card-white); }

  .identity {
    position: absolute; right: 489px; top: 292px; text-align: right;
  }
  .identity__name {
    color: var(--accent-red); font-size: 29px; font-weight: 400; line-height: 1.1;
  }
  .identity__role { font-size: 21px; font-weight: 400; line-height: 1.2; }

  .divider {
    position: absolute; left: 344px; top: 176px; width: 2px; height: 104px;
    background: var(--rule);
  }

  .contacts { position: absolute; left: 374px; top: 176px; list-style: none; }
  .contacts__item {
    display: flex; align-items: center; height: 25.5px;
    font-size: 20px; font-weight: 400; letter-spacing: 0.2px;
  }
  .contacts__icon { width: 18px; height: 18px; margin-right: 11px; fill: var(--accent-red); }

  .address {
    position: absolute; left: 0; right: 0; top: 383px; text-align: center;
    font-size: 20px; font-weight: 400;
  }

  .portrait {
    position: absolute; left: 299px; top: 69px; width: 204px; height: 258px;
    background: radial-gradient(ellipse at 50% 60%, #2a2a2a 0%, #555 70%, #bdbdbd 100%);
    border-radius: 40% 40% 12% 12%;
  }
  .brand-name {
    position: absolute; left: 0; right: 0; top: 324px; text-align: center;
    font-size: 42px; font-weight: 300; color: var(--text-black); letter-spacing: 1px;
  }
</style>
</head>
<body>
<main class="canvas">
  <section class="card card--front">
    <div class="identity">
      <p class="identity__name">Marc Ravoulet</p>
      <p class="identity__role">Magician</p>
    </div>
    <div class="divider"></div>
    <ul class="contacts">
      <li class="contacts__item">
        <svg class="contacts__icon" viewBox="0 0 24 24"><path d="M6.6 10.8a15.1 15.1 0 0 0 6.6 6.6l2.2-2.2a1 1 0 0 1 1-.25 11.4 11.4 0 0 0 3.6.57 1 1 0 0 1 1 1V20a1 1 0 0 1-1 1A17 17 0 0 1 3 4a1 1 0 0 1 1-1h3.5a1 1 0 0 1 1 1c0 1.25.2 2.45.57 3.6a1 1 0 0 1-.25 1z"/></svg>
        0381 946 157
      </li>
      <li class="contacts__item">
        <svg class="contacts__icon" viewBox="0 0 24 24"><path d="M6.6 10.8a15.1 15.1 0 0 0 6.6 6.6l2.2-2.2a1 1 0 0 1 1-.25 11.4 11.4 0 0 0 3.6.57 1 1 0 0 1 1 1V20a1 1 0 0 1-1 1A17 17 0 0 1 3 4a1 1 0 0 1 1-1h3.5a1 1 0 0 1 1 1c0 1.25.2 2.45.57 3.6a1 1 0 0 1-.25 1z"/></svg>
        0674 219 503
      </li>
      <li class="contacts__item">
        <svg class="contacts__icon" viewBox="0 0 24 24"><path d="M2 6h20v12H2z M2 6l10 7 10-7" fill="var(--accent-red)"/><path d="M3 7l9 6 9-6" fill="none" stroke="#000" stroke-width="1.5"/></svg>
        contact@verlindoillusions.example
      </li>
      <li class="contacts__item">
        <svg class="contacts__icon" viewBox="0 0 24 24"><circle cx="12" cy="12" r="10"/><path d="M2 12h20M12 2c3 3 3 17 0 20M12 2c-3 3-3 17 0 20" fill="none" stroke="#000" stroke-width="1.3"/></svg>
        www.verlindoillusions.example
      </li>
    </ul>
    <p class="address">MAGICIAN VERLINDO 17 rue des Tilleuls - 25000 BESANÇON</p>
  </section>

  <section class="card card--back">
    <div class="portrait" role="img" aria-label="Illustration of the magician holding a playing card"></div>
    <p class="brand-name">VERLINDO</p>
  </section>
</main>
</body>
</html>
```